Brenlow Estates Website and Logo Design

We need a new logo and website designed for 'Brenlow Estates Ltd', which is a well established Guernsey property holding company founded in 1934.

The company does not currently have a website. The new website should be similar in style and layout to https://www.quorvanhall.example/.

Target Market(s)

Industry, Media, Tenants

Industry/Entity Type

Property Management

Logo Text

BEL OR Brenlow Estates Ltd OR BE

Coding

Coded - Design and coding required

Number of Pages Required

4 page

Font styles to use
Other font styles liked:
• Helvetica

Requirements
Must have
• The logo laying over the picture (like https://www.quorvanhall.example/).
• Big pictures on homepage (like https://www.quorvanhall.example/)

```html
<!DOCTYPE html>
<html lang="en">
<head>
<meta charset="utf-8">
<title>Brenlow Estates Ltd</title>
<link rel="stylesheet" href="https://fonts.googleapis.com/css2?family=Marcellus&family=Arimo:wght@400&family=Open+Sans:wght@400;600&family=Pinyon+Script&display=swap">
<style>
:root{
  --teal:#2bc0b4;
  --ink:#1c2230;
  --grey-bg:#efefef;
  --text:#555b63;
  --white:#ffffff;
  --black:#0b0b0b;
  --footer-text:#e2e2e2;
  --footer-muted:#b9b9b9;
}
*{box-sizing:border-box;margin:0;padding:0}
html,body{width:1200px;height:3015px;overflow:hidden}
body{position:relative;background:var(--white);font-family:"Open Sans",Arial,sans-serif;color:var(--text)}
h1,h2,h3,h4{font-weight:400}
.abs{position:absolute}
.script{font-family:"Pinyon Script",cursive;font-size:22px;color:var(--ink);text-align:center;width:100%}
.section-title{font-family:"Arimo",Helvetica,sans-serif;font-weight:400;font-size:36px;color:var(--teal);text-align:center;width:100%}

/* hero */
.hero{left:0;top:0;width:1200px;height:678px;background:linear-gradient(180deg,#27344c 0%,#34465e 45%,#2b3b4a 70%,#1d2a33 100%)}
.brand{left:78px;top:22px;display:flex;align-items:center;gap:14px;color:var(--white)}
.brand-mark{width:84px;height:84px;border:3px solid var(--white);border-radius:50%;flex:none}
.brand-name{font-family:"Marcellus",Georgia,serif;font-size:30px;line-height:1;white-space:nowrap}
.nav{left:540px;top:14px;width:620px;height:84px}
.nav a{position:absolute;top:0;height:84px;line-height:84px;font-size:16px;color:var(--teal);text-decoration:none;transform:translateX(-50%)}
.nav a.current{width:88px;height:88px;line-height:84px;border:2px solid var(--white);border-radius:50%;color:var(--white);text-align:center}
.hero-tag{top:282px;width:100%;text-align:center;font-family:"Pinyon Script",cursive;font-size:22px;color:var(--white)}
.hero-title{top:306px;width:100%;text-align:center;font-family:"Marcellus",Georgia,serif;font-size:62px;color:var(--white);letter-spacing:1px}
.btn-white{left:522px;top:396px;width:156px;height:48px;background:var(--white);color:var(--ink);border-radius:3px;font-size:18px;text-align:center;line-height:48px}

/* welcome */
.welcome-script{top:726px}
.welcome-title{top:748px}
.welcome-text{left:150px;top:810px;width:900px;text-align:center;font-size:15.5px;line-height:22px}
.btn-black{left:528px;top:924px;width:144px;height:44px;background:var(--black);color:var(--white);border-radius:4px;font-size:16px;text-align:center;line-height:44px}

/* why */
.why{left:0;top:1020px;width:1200px;height:336px;background:linear-gradient(180deg,#1b2233 0%,#26334a 60%,#2f3f52 100%)}
.why-script{top:1074px;color:var(--white)}
.why-title{top:1090px}
.why-text{left:110px;top:1150px;width:980px;text-align:center;color:#e3e6ea;font-size:15px;line-height:26px}
.card{top:1240px;width:344px;height:262px;border:2px solid var(--ink);text-align:center;color:var(--ink)}
.card.teal{background:linear-gradient(180deg,#46cfc3 0%,#3ec7bb 60%,#2fb3a8 100%)}
.card.dark{background:linear-gradient(180deg,#2a3447 0%,#1d2636 100%);color:var(--white);border-color:#cfd3d8}
.card h3{margin-top:40px;font-family:"Marcellus",Georgia,serif;font-size:38px}
.card p{margin:12px auto 0;width:270px;font-size:14px;line-height:20px}
.card .card-btn{margin:26px auto 0;width:156px;height:46px;border:2px solid currentColor;line-height:42px;font-size:18px}

/* testimonial */
.testimonial{left:0;top:1554px;width:1200px;height:314px;background:var(--grey-bg)}
.t-script{top:1596px}
.t-title{top:1622px}
.avatar{left:76px;top:1684px;width:136px;height:136px;border-radius:50%;border:4px solid var(--teal);background:radial-gradient(circle at 50% 40%,#9aa7b3 0%,#5d6b78 60%,#2e3944 100%)}
.quote{left:236px;top:1708px;width:560px;font-size:15px;line-height:23px}
.client-name{left:870px;top:1716px;font-family:"Marcellus",Georgia,serif;font-size:18px;color:var(--ink)}
.client-role{left:884px;top:1746px;font-size:13px;color:#8a8f96;letter-spacing:1px}
.dots{left:888px;top:1804px;display:flex;gap:6px}
.dots span{width:10px;height:10px;border-radius:50%;border:1.5px solid var(--ink)}
.dots span.on{background:var(--ink)}

/* projects */
.p-script{top:1906px}
.p-title{top:1932px}
.tile{position:absolute}
.tile-feature{left:78px;top:2220px;width:694px;height:206px;background:linear-gradient(180deg,#3b4238 0%,#2b3230 100%);text-align:center;color:var(--white)}
.tile-feature h4{margin-top:44px;font-family:"Marcellus",Georgia,serif;font-size:21px;line-height:28px}
.tile-feature .card-btn{margin:20px auto 0;width:156px;height:46px;border:2px solid var(--white);line-height:42px;font-size:18px}

/* footer */
.footer{left:0;top:2552px;width:1200px;height:414px;background:linear-gradient(180deg,#2c2a27 0%,#1d1c1b 100%)}
.badge{left:524px;top:2476px;width:152px;height:152px;border-radius:50%;background:var(--white);border:10px solid var(--white)}
.badge-inner{width:100%;height:100%;border-radius:50%;border:4px solid var(--teal)}
.f-head{top:2658px;font-family:"Marcellus",Georgia,serif;font-size:19px;color:var(--white);letter-spacing:.5px}
.news{left:80px;width:246px;font-size:14px;line-height:20px;color:var(--footer-text)}
.news small{display:block;font-size:13px;color:var(--footer-muted);margin-top:2px}
.rule{left:80px;width:246px;height:1px;background:#8a8a8a}
.view-all{left:80px;top:2890px;font-family:"Marcellus",Georgia,serif;font-size:18px;color:var(--white);border-bottom:2px solid var(--white);line-height:22px}
.links{left:394px;top:2694px;font-size:14px;line-height:25px;list-style:none;color:var(--footer-text)}
.links li::before{content:"›";color:var(--footer-muted);margin-right:12px}
.contact{left:620px;font-size:15px;line-height:22px;display:flex;gap:14px;color:var(--footer-text)}
.contact svg{flex:none;margin-top:4px}
.contact-rule{left:604px;top:2806px;width:240px;height:1px;background:#6a6a6a}
.f-brand{left:926px;top:2648px;display:flex;align-items:center;gap:10px;color:var(--white)}
.f-brand .brand-mark{width:50px;height:50px;border-width:2px}
.f-brand .brand-name{font-size:20px}
.f-about{left:938px;top:2730px;width:190px;font-size:15px;line-height:22px;color:var(--teal)}
.social{top:2816px;width:50px;height:50px;border-radius:50%;border:2px solid var(--footer-muted);color:var(--white);font-size:12px;line-height:46px;text-align:center}
.social.active{background:var(--teal);border-color:var(--teal)}
.copyright{left:0;top:2966px;width:1200px;height:49px;background:var(--black);color:var(--white);text-align:center;line-height:49px;font-size:15px}
</style>
</head>
<body>

<!-- hero -->
<section class="abs hero" role="img" aria-label="Photograph of a harbour town at dusk with boats moored along the quay"></section>
<div class="abs brand"><span class="brand-mark"></span><span class="brand-name">Brenlow Estates Ltd</span></div>
<nav class="abs nav">
  <a class="current" style="left:44px">HOME</a>
  <a style="left:160px">ABOUT</a>
  <a style="left:290px">PROJECTS</a>
  <a style="left:418px">NEWS</a>
  <a style="left:542px">CONTACT</a>
</nav>
<p class="abs hero-tag">How innovation , not regulation can improve public health</p>
<h1 class="abs hero-title">REAL HOMES</h1>
<div class="abs btn-white">READ MORE</div>

<!-- welcome -->
<p class="abs script welcome-script">Welcome to Our Site</p>
<h2 class="abs section-title welcome-title">Brenlow Estates Limited</h2>
<p class="abs welcome-text">Brenlow Estates Limited (BEL) is a family-owned Guernsey property holding company. It purchases properties that are considered to have potential for development either through refurbishment or by obtaining planning permission to change its classification from, for example, industrial premises to offices or retail outlets, or by the marriage value of buying an adjacent property to one already owned by BEL.</p>
<div class="abs btn-black">READ MORE</div>

<!-- why guernsey -->
<section class="abs why" role="img" aria-label="Photograph of a city skyline at night"></section>
<p class="abs script why-script">Why Us?</p>
<h2 class="abs section-title why-title">Why Guernsey?</h2>
<p class="abs why-text">The Bailiwick of Guernsey is a British Crown dependency in the English Channel. The benefit of establishing a company in Guernsey is the island’s low tax jurisdiction since there are no capital taxes and no corporation taxes for many companies.</p>

<div class="abs card teal" style="left:78px" role="group" aria-label="Card over a photograph of a tropical garden">
  <h3>YESTERDAY</h3>
  <p>BEL was founded in 1934 by Edmund Brenlow to manage both his own extensive...</p>
  <div class="card-btn">VIEW DETAIL</div>
</div>
<div class="abs card dark" style="left:428px" role="group" aria-label="Card over a photograph of a harbour">
  <h3>TODAY</h3>
  <p>The Brenlow family has steadily built on the foundations set out by the founder ...</p>
  <div class="card-btn">VIEW DETAIL</div>
</div>
<div class="abs card teal" style="left:778px" role="group" aria-label="Card over a photograph of palm trees and a resort">
  <h3>TOMORROW</h3>
  <p>In keeping with its past project development philosophy, its intrinsic...</p>
  <div class="card-btn">VIEW DETAIL</div>
</div>

<!-- testimonial -->
<section class="abs testimonial"></section>
<p class="abs script t-script">What Our Client Say...</p>
<h2 class="abs section-title t-title">Testimonial</h2>
<div class="abs avatar" role="img" aria-label="Portrait photograph of a client"></div>
<p class="abs quote">"Lorem Ipsum is simply dummy text of the printing and typesetting industry. Lorem Ipsum has been the industry's standard dummy text ever since the 1500s, when an unknown printer took a galley of type and scrambled it to make a type specimen book."</p>
<svg class="abs" style="left:830px;top:1676px" width="24" height="156" viewBox="0 0 24 156" aria-hidden="true">
  <polyline points="12,0 12,46 20,54 12,62 12,156" fill="none" stroke="#2bc0b4" stroke-width="2.5"/>
</svg>
<p class="abs client-name">- Client's Name</p>
<p class="abs client-role">POSITION</p>
<div class="abs dots"><span class="on"></span><span></span><span></span><span></span></div>

<!-- projects -->
<p class="abs script p-script">Our Work...</p>
<h2 class="abs section-title p-title">Our Projects</h2>
<div class="tile" style="left:78px;top:2004px;width:344px;height:208px;background:linear-gradient(135deg,#d9d4cc 0%,#9aa0a3 55%,#5d6366 100%)" role="img" aria-label="Photograph of a bright living room with ocean view"></div>
<div class="tile" style="left:426px;top:2004px;width:346px;height:208px;background:linear-gradient(160deg,#e3e5e4 0%,#6f8a5b 55%,#3f5a35 100%)" role="img" aria-label="Photograph of a modern house beside green hills and a lake"></div>
<div class="tile" style="left:778px;top:2004px;width:344px;height:208px;background:linear-gradient(180deg,#b9cde0 0%,#d9dee2 55%,#5a8fa8 100%)" role="img" aria-label="Photograph of a curved waterfront apartment building with pool"></div>
<div class="tile tile-feature" role="group" aria-label="Photograph of high-rise towers among trees">
  <h4>LOREM IPSUM IS SIMPLY DUMMY TEXT OF PRINTING<br>AND TYPESETTING INDUSTRY</h4>
  <div class="card-btn">VIEW DETAIL</div>
</div>
<div class="tile" style="left:778px;top:2220px;width:344px;height:206px;background:linear-gradient(180deg,#c6b8a8 0%,#d7a878 55%,#a9683a 100%)" role="img" aria-label="Photograph of a terrace overlooking the sea at sunset"></div>

<!-- footer -->
<section class="abs footer" role="img" aria-label="Photograph of a city skyline at dusk"></section>
<div class="abs badge"><div class="badge-inner"></div></div>

<h3 class="abs f-head" style="left:80px">Latest News</h3>
<p class="abs news" style="top:2694px">Lorem Ipsum is simply dummy text of the printing and typesetting.<small>29th Nov,2016</small></p>
<div class="abs rule" style="top:2762px"></div>
<p class="abs news" style="top:2774px">Lorem Ipsum is simply dummy text of the printing and typesetting.<small>20th Nov,2016</small></p>
<div class="abs rule" style="top:2842px"></div>
<p class="abs view-all">View All »</p>

<h3 class="abs f-head" style="left:394px">Useful Links</h3>
<ul class="abs links">
  <li>Home</li><li>About us</li><li>Project</li><li>Testimonial</li><li>News</li><li>Contact Us</li>
</ul>

<h3 class="abs f-head" style="left:620px">Get in touch with us</h3>
<div class="abs contact" style="top:2696px">
  <svg width="14" height="20" viewBox="0 0 14 20" aria-hidden="true"><path d="M7 0a7 7 0 0 0-7 7c0 5 7 13 7 13s7-8 7-13a7 7 0 0 0-7-7zm0 10a3 3 0 1 1 0-6 3 3 0 0 1 0 6z" fill="#e2e2e2"/></svg>
  <span>123,Lorem Ipsum,<br>Country,Zip Code.</span>
</div>
<div class="abs contact" style="top:2772px">
  <svg width="16" height="16" viewBox="0 0 16 16" aria-hidden="true"><path d="M3.5 0.5l2.5 3-1.6 2a9 9 0 0 0 6 6l2-1.6 3 2.5-1.8 2.8C7 15 1 9 .7 2.3z" fill="#e2e2e2"/></svg>
  <span>123 456 7878</span>
</div>
<div class="abs contact-rule"></div>
<div class="abs contact" style="top:2814px">
  <svg width="18" height="14" viewBox="0 0 18 14" aria-hidden="true"><rect x="1" y="1" width="16" height="12" fill="none" stroke="#e2e2e2" stroke-width="1.5"/><polyline points="1,1 9,8 17,1" fill="none" stroke="#e2e2e2" stroke-width="1.5"/></svg>
  <span>info@brenlowestates.example</span>
</div>

<div class="abs f-brand"><span class="brand-mark"></span><span class="brand-name">Brenlow Estates Ltd</span></div>
<p class="abs f-about">Lorem Ipsum is simply dummy text of the printing and typesetting.</p>
<a class="abs social active" style="left:946px">Page</a>
<a class="abs social" style="left:1008px">Feed</a>
<a class="abs social" style="left:1070px">Clips</a>

<div class="abs copyright">© <b>Brenlow Estates Ltd.</b> - 2016 All Right Reserved.</div>

</body>
</html>
```